Website for Barlow Fabrication & Building Ltd

General Note to all.

1. Piling and gas works are separate areas of work and should not be put together.
- the marine section should really be the piling works and should have all the barges/water piles etc.
- the gas section should have the big silo looking thing

2. I would like to add in Specialist Onsite Labour and Management in the 'our services' section. The would include the Supervisors, Coded Welders, Site Fitters and Crane and Rig Crews etc.

3. I did like it how someone had use the BFB header logo as the top of the webpage with the individual tabs above and the website starting below. Please remove the VAT number and phone number from this section.

4. I also liked how one designer incorporate the orange line with spark (from the logo) as a page separator representing the welding part of the business

5. Add in a Mission Statement - To go above and beyond in to ensure our clients projects are delivered safely, ahead of schedule, in any environment for the benefit of not only our customers but also our employees and communities we work in.

6. Add in Business Objectives -BFB is on a mission to be one of the leading contractors in UK to supply All Site Labour - ranging from Site Management, fully Coded Welders, Site Fitters and Crane and Rig Crews.

7. I am happy for you to add in photos that are not ours for the thumbs nails for the our services. ie a colourful welding pics/cool tunnelling pic etc - just make sure I will not get done for copy write infringements

8. I would like a some type of 'contact us' field or 'request a consultation' section.

9. Please confirm if the webpages you create will be compatible for both desktop and mobile app and how difficult it will be to update personally once it is live.

10. You have all done very well and have thus far been very impressed with what you have produced. I gave a very vague brief as I was not entirely sure how you would go about making something with very little information. Some of the designs look very professional.

11. I'm not sure how once I choose the winning design how that then transfers over to my domain? Perhaps someone can help me with that? I will also be looking for a web hosting platform so feel free to provide this information.

After using Sketch hive for successful getting a professional logo for the company I'm giving the web design option a go.

I am looking for a professional website for the above civil construction company.

The company director has many years experience in Marine, tunnelling, conveyors, stadium construction gas and piling works including piling works for coal ports, bridges and tunnels.

The company currently provide 20+ skilled and experienced guys from all trades (supervisors, coded welders, fitters, crane drivers and crane supervisors, rigglers, slingers and piling operatives) on the Corran Shoreline project in London - London's new super sewer. Most of this work is off barges carrying cranes (upto 600T and drill rigs).

As we are looking to expand and get more subcontracts we need a web presence to say who we are and what we do.

I'll include the 2 company logos we currently use below

I have included an info doc with pics you may or may not use.

Target Market(s)

Mainly other large construction companies and potential subcontractors

Industry/Entity Type

Construction Company

Coding

Coded - Design and coding required

Font styles to use
Sans Serif

Colors
0655a3
f37122
ffffff

Requirements
Must have
• Few tabs
• Simple to use/update but still professional look
• The challenge will be making the website look professional with not much available content.
Should not have
• No residential house building

```html
<!DOCTYPE html>
<html lang="en">
<head>
<meta charset="utf-8">
<title>Barlow Fabrication & Building Ltd</title>
<link rel="stylesheet" href="https://fonts.googleapis.com/css2?family=Lato:wght@400;700;900&family=Poppins:wght@400;500;600&display=swap">
<style>
:root{
  --blue:#0655a3;
  --navy:#173a6a;
  --deep:#0f2a4e;
  --orange:#f37122;
  --spark:#ffc233;
  --white:#ffffff;
  --ink:#2b2b2b;
  --grey:#666;
  --light:#f4f5f7;
}
*{box-sizing:border-box;margin:0;padding:0}
html,body{width:1200px;height:3841px;overflow:hidden;background:var(--white)}
body{font-family:"Lato",Arial,sans-serif;color:var(--ink)}
.canvas{position:relative;width:1200px;height:3841px;overflow:hidden}
.abs{position:absolute}
.section-title{position:absolute;left:0;width:100%;text-align:center;font-weight:900;font-size:19px;letter-spacing:.5px;text-transform:uppercase}
.btn{display:inline-block;background:var(--orange);color:var(--white);font-weight:700;font-size:11px;text-transform:uppercase;border-radius:3px;text-align:center}

/* top bar */
.topbar{left:0;top:0;width:1200px;height:37px;background:var(--navy);color:var(--white);font-size:11px;font-weight:700}
.topbar .mail{left:528px;top:12px}
.topbar .consult{right:0;top:0;width:212px;height:37px;line-height:37px;border-radius:0;font-size:10px}
.topbar svg{vertical-align:-2px;margin-right:5px}

/* nav */
.nav{left:0;top:37px;width:1200px;height:113px;background:var(--white)}
.nav a{position:absolute;top:56px;font-family:"Poppins",Arial,sans-serif;font-size:12px;font-weight:500;color:var(--navy);text-decoration:none}
.nav a.active{color:var(--orange);border:1px solid var(--orange);border-radius:4px;padding:4px 12px;top:51px}
.brand{left:510px;top:37px;width:180px;height:126px;border-radius:0 0 90px 90px;background:var(--white);z-index:5;text-align:center}
.brand .dot{position:absolute;left:68px;top:8px;width:44px;height:44px;border-radius:50%;background:var(--orange)}
.brand .name{position:absolute;left:0;top:56px;width:100%;font-weight:900;font-size:38px;color:var(--navy);letter-spacing:2px}

/* hero */
.hero{left:0;top:150px;width:1200px;height:430px}
.hero .photo{position:absolute;inset:0;background:linear-gradient(180deg,#cfe0f2 0%,#a7c3e2 40%,#8a6d55 62%,#3d4654 78%,#273346 100%)}
.hero h1{position:absolute;left:144px;top:128px;font-size:29px;font-weight:900;color:var(--blue);letter-spacing:.5px}
.hero h1 span{color:var(--orange)}
.hero p{position:absolute;left:144px;top:175px;width:430px;font-size:12px;line-height:18px;color:var(--white)}
.hero .btn{position:absolute;left:144px;top:232px;width:124px;height:34px;line-height:34px;border-radius:17px}
.arrow{position:absolute;top:168px;width:26px;height:30px;background:rgba(255,255,255,.7);border-radius:2px}
.arrow svg{display:block;margin:8px auto}

/* about */
.about-frame{left:150px;top:626px;width:360px;height:280px;border-top:2px solid #c9c9c9;border-left:2px solid #c9c9c9}
.about-photo{left:131px;top:640px;width:371px;height:288px;background:linear-gradient(180deg,#dbe7f3 0%,#a9bccd 45%,#6c6a5c 70%,#3b4450 100%);box-shadow:0 3px 10px rgba(0,0,0,.2)}
.about h2{position:absolute;left:549px;top:660px;font-size:21px;font-weight:900;color:var(--navy);text-transform:uppercase}
.about p{position:absolute;left:553px;width:530px;font-size:11.5px;line-height:16px;color:var(--grey)}
.about .label{position:absolute;left:553px;font-size:12px;font-weight:900;color:var(--orange);text-transform:uppercase;letter-spacing:.3px}
.about .more{position:absolute;left:556px;top:900px;font-size:12px;font-weight:700;color:var(--navy);border-bottom:1px solid var(--navy)}

/* sectors */
.sectors{left:0;top:930px;width:1200px;height:440px;background:linear-gradient(180deg,#2c5a8f 0%,#1f4b80 50%,#173f70 100%)}
.sectors .section-title{top:134px;color:var(--white)}
.sector{position:absolute;top:222px;width:150px;text-align:center;color:var(--white);font-size:11px;font-weight:700;text-transform:uppercase}
.sector .icon{width:86px;height:86px;margin:0 auto 12px;border:2px solid rgba(255,255,255,.85);border-radius:14px;display:flex;align-items:center;justify-content:center}

/* team */
.team-title{top:1414px;color:var(--navy)}
.member{position:absolute;top:1466px;width:196px}
.member .pic{height:129px;background:linear-gradient(180deg,#bcd2e8,#7e97b3)}
.member h4{margin-top:20px;font-size:12px;font-weight:700;color:var(--ink)}
.member span{font-size:10px;color:var(--grey)}

/* projects */
.projects{left:0;top:1700px;width:1200px;height:626px;background:linear-gradient(180deg,#1e4e86 0%,#1a4679 100%)}
.projects .section-title{top:40px;color:var(--white)}
.filters{position:absolute;left:0;top:100px;width:100%;display:flex;justify-content:center;gap:22px;font-size:11px;color:var(--white)}
.filters span{padding:4px 8px}
.filters .on{background:var(--orange);border-radius:3px}
.tile{position:absolute;width:293px;height:183px;background:linear-gradient(180deg,#9fb8d0,#5b6b78 60%,#36404c)}
.tile.feature{background:var(--white);text-align:center;padding:42px 22px 0}
.tile.feature h3{font-size:16px;font-weight:900;color:var(--ink)}
.tile.feature p{font-size:11px;line-height:15px;color:var(--grey);margin:10px 0 12px}
.tile.feature .btn{width:104px;height:28px;line-height:28px}

/* testimonials */
.testi{left:0;top:2326px;width:1200px;height:400px;background:linear-gradient(180deg,#f37122,#ee6a1e)}
.testi .section-title{top:44px;color:var(--white)}
.card{position:absolute;top:136px;height:152px;border:1px solid rgba(255,255,255,.8);border-radius:12px;text-align:center;color:var(--white);padding:48px 18px 0}
.card .avatar{position:absolute;left:50%;top:-18px;width:50px;height:50px;margin-left:-25px;border-radius:50%;background:#c9b7a8;border:3px solid var(--white)}
.card p{font-size:11px;line-height:15px}
.card h5{margin-top:16px;font-size:12px;font-weight:700}
.tarrow{position:absolute;top:206px;width:22px;height:22px;border-radius:50%;background:rgba(255,255,255,.35)}
.tarrow svg{display:block;margin:6px auto}

/* blog */
.blog{left:0;top:2719px;width:1200px;height:316px;background:var(--light)}
.blog .section-title{top:66px;color:var(--ink);font-size:18px}
.post-img{position:absolute;top:151px;width:188px;height:162px;background:linear-gradient(180deg,#9cb7d1,#6a5d4c 65%,#3b3f45)}
.post{position:absolute;top:177px;width:248px;height:118px;background:var(--white);box-shadow:0 2px 10px rgba(0,0,0,.15);padding:14px 14px}
.post h5{font-size:12px;font-weight:700}
.post .date{font-size:9px;color:var(--grey)}
.post p{font-size:10px;line-height:14px;color:var(--grey);margin:6px 0 4px}
.post .more{font-size:10px;font-weight:700;color:var(--ink)}

/* skyline + clients */
.skyline{left:0;top:3035px;width:1200px;height:130px;background:linear-gradient(180deg,#f4f5f7 0%,#8fa9c8 55%,#1f4a80 100%)}
.clients{left:0;top:3163px;width:1200px;height:240px;background:#1f4a80}
.clients .section-title{top:42px;color:var(--white);font-size:18px}
.client{position:absolute;top:112px;width:132px;height:74px;background:var(--white);display:flex;align-items:center;justify-content:center;gap:7px;font-weight:900;font-size:15px;color:var(--navy)}
.client i{display:inline-block;width:12px;height:12px;background:var(--orange)}

/* footer */
.footer{left:0;top:3385px;width:1200px;height:456px;background:linear-gradient(180deg,#1c2c45,#141f31);color:#cfd6e0}
.footer h6{position:absolute;top:100px;font-size:11px;font-weight:700;color:var(--white);text-transform:uppercase}
.links{position:absolute;left:149px;top:127px;list-style:none;font-size:11px;line-height:20px}
.contact{position:absolute;left:353px;top:125px;font-size:11px;line-height:16px}
.contact div{position:relative;padding-left:26px;margin-bottom:22px}
.contact svg{position:absolute;left:0;top:2px}
.social{position:absolute;left:567px;top:128px;display:flex;gap:7px}
.social span{width:16px;height:16px;border-radius:50%;background:var(--blue)}
.form{position:absolute;left:805px;top:123px;width:245px}
.form .field{height:30px;border:1px solid rgba(255,255,255,.35);margin-bottom:12px;font-size:10px;padding:9px 10px;color:#9aa6b6}
.form .field.msg{height:46px}
.form .send{width:72px;height:26px;line-height:24px;border:1px solid var(--orange);color:var(--white);font-size:9px;font-weight:700;text-align:center;margin-top:8px}
.copy{position:absolute;left:149px;top:431px;font-size:9px;color:#9aa6b6}
</style>
</head>
<body>
<div class="canvas">

  <!-- Top bar -->
  <div class="abs topbar">
    <span class="abs mail"><svg width="11" height="11" viewBox="0 0 12 12"><path d="M1 6 11 1 8 11 6 7Z" fill="#fff"/></svg>E-Mail us : info@bfb.com</span>
    <span class="abs btn consult">Request a Consultation</span>
  </div>

  <!-- Navigation -->
  <nav class="abs nav">
    <a class="active" style="left:150px">Home</a>
    <a style="left:232px">About us</a>
    <a style="left:322px">What we do</a>
    <a style="left:422px">Services</a>
    <a style="left:701px">Our Projects</a>
    <a style="left:815px">Our Team</a>
    <a style="left:906px">Blog</a>
    <a style="left:975px">Contact us</a>
  </nav>
  <div class="abs brand"><span class="dot"></span><span class="name">BFB</span></div>

  <!-- Hero -->
  <section class="abs hero">
    <div class="photo" role="img" aria-label="Piling barge with crane on the river at dusk"></div>
    <div class="arrow" style="left:86px"><svg width="8" height="12" viewBox="0 0 8 12"><path d="M7 1 2 6l5 5" stroke="#333" stroke-width="2" fill="none"/></svg></div>
    <div class="arrow" style="left:1080px"><svg width="8" height="12" viewBox="0 0 8 12"><path d="M1 1l5 5-5 5" stroke="#333" stroke-width="2" fill="none"/></svg></div>
    <h1>BUILDING <span>BETTER, FASTER</span></h1>
    <p>Lorem ipsum dolor sit amet, consectetuer adipiscing elit. Aenean commodo ligula eget dolor. Aenean massa cum sociis natoque penatibus.</p>
    <span class="btn">Read More</span>
    <svg class="abs" style="left:0;bottom:-1px" width="1200" height="60" viewBox="0 0 1200 60" preserveAspectRatio="none">
      <path d="M0 40 C300 0 600 70 900 30 S1150 20 1200 30 V60 H0Z" fill="#fff"/>
    </svg>
  </section>

  <!-- About -->
  <section class="about">
    <div class="abs about-frame"></div>
    <div class="abs about-photo" role="img" aria-label="Crane barge working beside a riverside site"></div>
    <h2>Barlow Fabrication &amp; Building</h2>
    <p style="top:696px">Barlow Fabrication &amp; Building has over 15 years experience in the civil construction industry. We are subcontracted to Halden Ostrand Joint Venture on the Corran Shoreline project in London, providing a highly skilled workforce, with a strong piling history in the UK and Australia.</p>
    <span class="label" style="top:752px">Our Mission</span>
    <p style="top:768px">To go above and beyond to ensure our clients' projects are delivered safely, ahead of schedule, in any environment, for the benefit of not only our customers but also our employees and the communities we work in.</p>
    <span class="label" style="top:824px">Business Objectives</span>
    <p style="top:840px">BFB is on a mission to be one of the leading contractors in the UK to supply all site labour, ranging from Site Management and fully Coded Welders to Site Fitters and Crane and Rig Crews.</p>
    <span class="more">Read More</span>
  </section>

  <!-- Sectors -->
  <section class="abs sectors" role="group" aria-label="Sectors">
    <svg class="abs" style="left:0;top:0" width="1200" height="70" viewBox="0 0 1200 70" preserveAspectRatio="none">
      <path d="M0 0 H1200 V20 C900 60 500 -10 0 50Z" fill="#fff"/>
      <path d="M0 50 C500 -10 900 60 1200 20" stroke="#f37122" stroke-width="4" fill="none"/>
    </svg>
    <svg class="abs spark" style="left:659px;top:12px" width="32" height="32" viewBox="0 0 32 32" aria-hidden="true">
      <g stroke="#ffc233" stroke-width="2" stroke-linecap="round"><path d="M16 2v8M16 22v8M2 16h8M22 16h8M6 6l5 5M21 21l5 5M26 6l-5 5M11 21l-5 5"/></g>
      <circle cx="16" cy="16" r="4" fill="#f37122"/>
    </svg>
    <h3 class="section-title">Sectors that we operate</h3>
    <div class="sector" style="left:134px"><div class="icon"><svg width="44" height="40" viewBox="0 0 44 40" fill="none" stroke="#fff" stroke-width="2.5"><path d="M6 26h32l-5 8H11Z"/><path d="M12 26V16h20v10M18 16V9h8v7"/><path d="M2 38c6-3 10 3 20 0s14 3 20 0"/></svg></div>Marine</div>
    <div class="sector" style="left:304px"><div class="icon"><svg width="40" height="40" viewBox="0 0 40 40" fill="none" stroke="#fff" stroke-width="2.5"><path d="M6 36V10h10v26M24 36V4h10v32M2 36h36"/><path d="M9 16h4M9 22h4M27 12h4M27 18h4M27 24h4"/></svg></div>Piling</div>
    <div class="sector" style="left:466px"><div class="icon"><svg width="40" height="40" viewBox="0 0 40 40" fill="none" stroke="#fff" stroke-width="2.5"><path d="M10 16a10 10 0 0 1 20 0Z"/><path d="M8 16h24"/><path d="M8 38c0-8 5-12 12-12s12 4 12 12"/></svg></div>Skilled<br>Labour</div>
    <div class="sector" style="left:618px"><div class="icon"><svg width="36" height="40" viewBox="0 0 36 40" fill="none" stroke="#fff" stroke-width="2.5"><path d="M4 38V6a3 3 0 0 1 3-3h12a3 3 0 0 1 3 3v32M2 38h22M8 10h10v8H8Z"/><path d="M22 14h5l3 4v14a2 2 0 0 0 4 0V12"/></svg></div>Gas<br>Works</div>
    <div class="sector" style="left:782px"><div class="icon"><svg width="44" height="40" viewBox="0 0 44 40" fill="none" stroke="#fff" stroke-width="2.5"><path d="M4 36V20a18 18 0 0 1 36 0v16Z"/><path d="M13 36V22a9 9 0 0 1 18 0v14"/></svg></div>Tunnelling</div>
    <div class="sector" style="left:931px"><div class="icon"><svg width="46" height="40" viewBox="0 0 46 40" fill="none" stroke="#fff" stroke-width="2.5"><path d="M10 6v30M36 6v30M2 14h42M2 26h42M10 14l8 12M36 14l-8 12"/></svg></div>Bridge &amp; Stadium<br>Construction</div>
  </section>

  <!-- Team -->
  <h3 class="section-title team-title">Our Team</h3>
  <div class="member" style="left:133px"><div class="pic" role="img" aria-label="Team member portrait"></div><h4>Owen R. Hale</h4><span>Company Director</span></div>
  <div class="member" style="left:369px"><div class="pic" role="img" aria-label="Team member portrait"></div><h4>Callum Brent</h4><span>Construction Manager</span></div>
  <div class="member" style="left:625px"><div class="pic" role="img" aria-label="Team member portrait"></div><h4>Neil Farrow</h4><span>Construction Manager</span></div>
  <div class="member" style="left:870px"><div class="pic" role="img" aria-label="Rigger working at height"></div><h4>Ryan Colby</h4><span>Rigger</span></div>

  <!-- Projects -->
  <section class="abs projects">
    <h3 class="section-title">Our Projects</h3>
    <div class="filters"><span class="on">All</span><span>Marine</span><span>Piling</span><span>Tunnelling</span><span>Gas works</span><span>Skilled Labour Supply</span><span>Bridge Construction</span><span>Stadium Construction</span></div>
    <div class="tile feature" style="left:131px;top:153px">
      <h3>London's new 'super sewer'</h3>
      <p>Lorem ipsum dolor sit amet, consectetuer adipiscing elit. Aenean commodo ligula eget dolor.</p>
      <span class="btn">Read More</span>
    </div>
    <div class="tile" style="left:457px;top:153px" role="img" aria-label="Piling barge moored on the river"></div>
    <div class="tile" style="left:776px;top:153px" role="img" aria-label="Steel tunnel shaft interior"></div>
    <div class="tile" style="left:131px;top:381px" role="img" aria-label="Sheet pile cofferdam wall"></div>
    <div class="tile" style="left:457px;top:381px" role="img" aria-label="Drill rig tower on site"></div>
    <div class="tile" style="left:776px;top:381px" role="img" aria-label="Riverside site at sunset"></div>
  </section>

  <!-- Testimonials -->
  <section class="abs testi">
    <h3 class="section-title">Client Testimonials</h3>
    <div class="tarrow" style="left:146px"><svg width="7" height="10" viewBox="0 0 7 10"><path d="M6 1 2 5l4 4" stroke="#fff" stroke-width="2" fill="none"/></svg></div>
    <div class="tarrow" style="left:1034px"><svg width="7" height="10" viewBox="0 0 7 10"><path d="M1 1l4 4-4 4" stroke="#fff" stroke-width="2" fill="none"/></svg></div>
    <div class="card" style="left:191px;width:259px"><span class="avatar" role="img" aria-label="Client portrait"></span><p>Lorem ipsum dolor sit amet, consectetuer adipiscing elit. Aenean commodo ligula eget dolor. Aenean</p><h5>Daniel Okafor</h5></div>
    <div class="card" style="left:473px;width:248px"><span class="avatar" role="img" aria-label="Client portrait"></span><p>Lorem ipsum dolor sit amet, consectetuer adipiscing elit. Aenean commodo ligula eget dolor. Aenean</p><h5>Priya</h5></div>
    <div class="card" style="left:755px;width:246px"><span class="avatar" role="img" aria-label="Client portrait"></span><p>Lorem ipsum dolor sit amet, consectetuer adipiscing elit. Aenean commodo ligula eget dolor. Aenean</p><h5>Maren</h5></div>
    <svg class="abs" style="left:0;bottom:-2px" width="1200" height="60" viewBox="0 0 1200 60" preserveAspectRatio="none">
      <path d="M0 20 C400 70 800 0 1200 40 V60 H0Z" fill="#f4f5f7"/>
      <path d="M0 20 C400 70 800 0 1200 40" stroke="#1f4a80" stroke-width="5" fill="none"/>
    </svg>
  </section>

  <!-- Blog -->
  <section class="abs blog">
    <h3 class="section-title">Latest Blog</h3>
    <div class="post-img" style="left:157px" role="img" aria-label="Drilling rig on a barge"></div>
    <div class="post" style="left:277px"><h5>Lorem ipsum dolor sit amet,</h5><div class="date">09-07-2019</div><p>Lorem ipsum dolor sit amet, consectetuer adipiscing elit. Aenean commodo ligula eget</p><span class="more">Read More</span></div>
    <div class="post-img" style="left:643px" role="img" aria-label="Steel pile frame on site"></div>
    <div class="post" style="left:758px"><h5>Lorem ipsum dolor sit amet,</h5><div class="date">09-07-2019</div><p>Lorem ipsum dolor sit amet, consectetuer adipiscing elit. Aenean commodo ligula eget</p><span class="more">Read More</span></div>
  </section>

  <!-- Clients -->
  <div class="abs skyline" role="img" aria-label="Silhouette of cranes and city skyline"></div>
  <section class="abs clients">
    <h3 class="section-title">Meet Our Clients</h3>
    <div class="client" style="left:133px"><i></i>Corran</div>
    <div class="client" style="left:298px">Vanta</div>
    <div class="client" style="left:463px">Norvane</div>
    <div class="client" style="left:628px">Fernbridge</div>
    <div class="client" style="left:776px">Corbel Civil</div>
    <div class="client" style="left:933px"><i></i>Kestrel</div>
  </section>

  <!-- Footer -->
  <footer class="abs footer">
    <svg class="abs" style="left:0;top:-2px" width="1200" height="60" viewBox="0 0 1200 60" preserveAspectRatio="none">
      <path d="M0 0 H1200 V30 C800 0 400 60 0 20Z" fill="#1f4a80"/>
      <path d="M0 20 C400 60 800 0 1200 30" stroke="#f37122" stroke-width="4" fill="none"/>
    </svg>
    <svg class="abs spark" style="left:584px;top:11px" width="32" height="32" viewBox="0 0 32 32" aria-hidden="true">
      <g stroke="#ffc233" stroke-width="2" stroke-linecap="round"><path d="M16 2v8M16 22v8M2 16h8M22 16h8M6 6l5 5M21 21l5 5M26 6l-5 5M11 21l-5 5"/></g>
      <circle cx="16" cy="16" r="4" fill="#f37122"/>
    </svg>
    <h6 style="left:149px">Quick Links</h6>
    <ul class="links"><li>Home</li><li>About us</li><li>What we do</li><li>Services we offer</li><li>Projects</li><li>Blog</li><li>Contact us</li></ul>
    <h6 style="left:353px">Contact Us</h6>
    <div class="contact">
      <div><svg width="12" height="14" viewBox="0 0 12 14"><path d="M6 0a5 5 0 0 1 5 5c0 4-5 9-5 9S1 9 1 5a5 5 0 0 1 5-5Z" fill="#fff"/><circle cx="6" cy="5" r="2" fill="#16243a"/></svg>14 Quarry Lane<br>Hexford HX4 2PL</div>
      <div><svg width="12" height="12" viewBox="0 0 12 12"><path d="M2 1h3l1 3-2 1a7 7 0 0 0 3 3l1-2 3 1v3c-6 0-9-3-9-9Z" fill="#fff"/></svg>+44 20 7946 0321</div>
      <div><svg width="13" height="10" viewBox="0 0 13 10"><rect x=".5" y=".5" width="12" height="9" fill="none" stroke="#fff"/><path d="M1 1l5.5 5L12 1" fill="none" stroke="#fff"/></svg>contact@bfb.com<br>info@bfb.com</div>
    </div>
    <h6 style="left:567px">Social Links</h6>
    <div class="social"><span></span><span></span><span></span><span></span></div>
    <h6 style="left:805px">Get in Touch</h6>
    <div class="form">
      <div class="field">Name</div>
      <div class="field">Phone</div>
      <div class="field">Email</div>
      <div class="field msg">Message</div>
      <div class="send">SEND ›</div>
    </div>
    <div class="copy">©2019 bfb.com. All Rights Reserved</div>
  </footer>

</div>
</body>
</html>
```